Redesign of business card for Cedar Ridge Mechanical

We are looking for a new design for our business cards for Cedar Ridge Mechanical. We are a plumbing & HVAC construction company, operating on the West Coast of Canada and USA. Logo attached.
Industry/Entity Type
Construction - Plumbing & HVAC
Contact Information for Business Card
Name, address, phone numbers, email, website address
Look and feel
Each slider illustrates characteristics of the customer's brand and the style your logo design should communicate.

```html
<!DOCTYPE html>
<html lang="en">
<head>
<meta charset="UTF-8">
<title>Cedar Ridge Mechanical – Business Card</title>
<link href="https://fonts.googleapis.com/css2?family=Poppins:wght@300;400;600&display=swap" rel="stylesheet">
<style>
  :root {
    --backdrop: #232323;
    --card: #1f1f21;
    --card-edge: #2a2a2d;
    --ink: #f4f4f4;
    --ink-soft: #d8d8d8;
    --emboss: #2e2e31;
    --ghost: rgba(255,255,255,0.06);
  }
  * { box-sizing: border-box; margin: 0; padding: 0; }
  html, body {
    width: 1200px; height: 780px; overflow: hidden;
    background: var(--backdrop);
    font-family: "Poppins", sans-serif;
  }
  .canvas {
    width: 1200px; height: 780px;
    display: flex; align-items: center; justify-content: center; gap: 48px;
  }
  .card {
    position: relative;
    width: 520px; height: 300px;
    background: var(--card);
    border: 1px solid var(--card-edge);
    border-radius: 3px;
    box-shadow: 0 18px 40px rgba(0,0,0,0.45);
    overflow: hidden;
  }

  /* Front */
  .brand {
    position: absolute; left: 34px; top: 30px;
    display: flex; align-items: center; gap: 12px;
  }
  .brand-mark {
    width: 26px; height: 26px;
    border: 2px solid var(--ink);
    border-radius: 4px;
  }
  .brand-name {
    font-weight: 600; font-size: 17px; letter-spacing: 0.5px;
    color: var(--ink); text-transform: uppercase;
  }
  .contact {
    position: absolute; left: 34px; top: 96px;
    list-style: none; color: var(--ink-soft);
    font-weight: 300; font-size: 13px; line-height: 21px;
  }
  .contact li { display: flex; align-items: center; gap: 8px; }
  .contact .address { padding-left: 22px; }
  .contact svg { width: 14px; height: 14px; flex: none; }
  .ghost-square {
    position: absolute; right: 40px; bottom: -30px;
    width: 230px; height: 190px;
    border: 14px solid var(--ghost);
    border-radius: 26px;
  }
  .person {
    position: absolute; right: 52px; bottom: 34px;
    text-align: right; color: var(--ink);
  }
  .person-name { font-size: 30px; line-height: 36px; font-weight: 300; }
  .person-name .first { font-weight: 600; }
  .person-title { font-size: 15px; font-weight: 300; color: var(--ink-soft); }
  .accent-bar {
    position: absolute; right: 0; bottom: 30px;
    width: 30px; height: 58px; background: var(--ink);
  }

  /* Back */
  .card-back { display: flex; align-items: center; justify-content: center; }
  .back-brand {
    display: flex; align-items: center; gap: 16px;
  }
  .back-brand .brand-mark { width: 38px; height: 38px; border-color: var(--emboss); border-width: 3px; border-radius: 6px; }
  .back-brand .brand-name { font-size: 26px; color: var(--emboss); }
</style>
</head>
<body>
<main class="canvas">
  <section class="card card-front">
    <div class="brand">
      <span class="brand-mark"></span>
      <span class="brand-name">Cedar Ridge Mechanical</span>
    </div>
    <ul class="contact">
      <li class="address">1840 Harbor Ln. Suite 310</li>
      <li class="address">Tacoma, WA 98402</li>
      <li>
        <svg viewBox="0 0 24 24" fill="currentColor"><path d="M6.6 10.8a15.1 15.1 0 0 0 6.6 6.6l2.2-2.2c.3-.3.7-.4 1-.2 1.1.4 2.3.6 3.6.6.6 0 1 .4 1 1V20c0 .6-.4 1-1 1A17 17 0 0 1 3 4c0-.6.4-1 1-1h3.5c.6 0 1 .4 1 1 0 1.3.2 2.5.6 3.6.1.3 0 .7-.2 1z"/></svg>
        (253) 555-0148
      </li>
      <li>
        <svg viewBox="0 0 24 24" fill="none" stroke="currentColor" stroke-width="2"><rect x="3" y="5" width="18" height="14" rx="1"/><path d="M3 6l9 7 9-7"/></svg>
        info@cedarridgemech.com
      </li>
      <li>
        <svg viewBox="0 0 24 24" fill="none" stroke="currentColor" stroke-width="2"><circle cx="12" cy="12" r="9"/><path d="M3 12h18M12 3c3 3 3 15 0 18M12 3c-3 3-3 15 0 18"/></svg>
        www.cedarridgemech.com
      </li>
    </ul>
    <div class="ghost-square"></div>
    <div class="person">
      <p class="person-name"><span class="first">Marta</span> Kovel</p>
      <p class="person-title">Founder &amp; CEO</p>
    </div>
    <div class="accent-bar"></div>
  </section>

  <section class="card card-back">
    <div class="back-brand">
      <span class="brand-mark"></span>
      <span class="brand-name">Cedar Ridge Mechanical</span>
    </div>
  </section>
</main>
</body>
</html>
```